Design a Website in Wordpress for an Australian Health Training Company in Health related courses

We require a WORDPRESS based Website (due to add on's we need to use for third party software) to replace our old site.
We offer national face to face delivery in medical reception, terminology and also administration.
The website will have around 6 pages and the ability to describe our main 6 courses (perhaps on the Courses page this may be tabs opening up to details for example?)
I have attached a previous sample of a Joomla site which was being developed (please do not feel you have to copy this - but I am just giving it as a sample - copying would be boring). But it gives an idea of look/feel and colours which may be suitable. Open to other ideas though.
I will provide some of the content, but would like the ability to finish the content myself.
Images and graphics are important. While a few medical photos re great - don't be tempted to us all pictures of doctors and nurses (although a couple would be good) - these are administrative courses so general corporate, eye catching visionary pictures of people in general are great. A medical type picture is also fine.
THE BOOKING system - will be via an ADD ON which will occur at the end of the project and is supplied by a third party software company (our student management system). This project will include up to 2 hours working with the Tech guys from the third party software to enable the ADD ON. If this ADD ON requires more time, we will pay hourly (although I do not expect it will).
Target Market(s)
Mostly a female market, many mature aged women target 25-45 yrs. Mixture of medical/health and corporate. Maybe a bit of mums returning to work and corporate inspiration.
Industry/Entity Type
It Company
Coding
Coded - Design and coding required
Number of Pages Required
5+ page
Requirements
Must have
- Wordpress
- Great graphics
- Interesting
- professional and clean
- Enquiry section (info Pak)
- Should have a University feel to it - Education
- Pages
- Home Page - About Us - Recruitment -Courses - Class Schedule - Traineeships Queensland Funding - Latest News Blog - Corporate Training- Contact us

```html
<!DOCTYPE html>
<html lang="en">
<head>
<meta charset="utf-8">
<title>Kestrel Institute of Training</title>
<link href="https://fonts.googleapis.com/css2?family=Cinzel:wght@400;700&family=Lato:ital,wght@0,400;0,700;1,400&display=swap" rel="stylesheet">
<style>
:root{
  --navy:#34466b;
  --navy-dark:#26344f;
  --tan:#c79a5e;
  --grey:#e8e8e8;
  --text:#444;
  --white:#fff;
}
*{box-sizing:border-box;margin:0;padding:0}
html,body{width:1200px;height:3947px;overflow:hidden}
body{font-family:'Lato',sans-serif;color:var(--text);background:var(--white);position:relative;font-size:14px}
.section{position:absolute;left:0;width:1200px;overflow:hidden}
.heading{font-family:'Cinzel',serif;font-size:32px;color:var(--navy);text-align:center;letter-spacing:1px}
.heading .accent{color:var(--tan)}
.heading-rule{width:130px;height:2px;background:var(--navy);margin:6px auto 0}
.btn{display:inline-block;background:var(--navy);color:var(--white);font-size:13px;padding:11px 24px;border-radius:2px}

/* brand name: one font, one weight, one colour */
.brand-name{font-family:'Lato',sans-serif;font-weight:700;color:var(--navy)}

/* top bar */
.topbar{top:0;height:40px;background:#f2f2f2}
.social{position:absolute;top:10px;display:flex;gap:5px}
.social span{width:20px;height:20px;background:var(--navy);display:block}
.topbar .info{position:absolute;top:12px;font-size:12px;color:#555;display:flex;align-items:center;gap:8px;white-space:nowrap}
.dot-icon{width:16px;height:16px;border-radius:50%;background:var(--navy);display:inline-block}
.account{position:absolute;left:820px;top:0;width:280px;height:40px;background:var(--navy);color:var(--white);font-size:13px;display:flex;align-items:center;gap:26px;padding-left:24px;letter-spacing:.5px}
.flag{width:22px;height:13px;background:#2a3e8c;display:inline-block;vertical-align:middle;margin-right:6px}

/* header */
.header{top:40px;height:86px;background:var(--white)}
.brand{position:absolute;left:100px;top:15px;display:flex;align-items:center;gap:12px}
.brand .mark{width:56px;height:56px;background:var(--navy)}
.brand .brand-name{font-size:14px;line-height:17px;width:130px}
.mainnav{position:absolute;right:100px;top:34px;display:flex;gap:40px;font-family:'Cinzel',serif;font-size:15px;color:#333}
.subnav{top:126px;height:48px;background:var(--navy)}
.subnav ul{list-style:none;display:flex;gap:74px;position:absolute;left:100px;top:15px;font-family:'Cinzel',serif;font-size:14px;color:var(--white);letter-spacing:.5px}
.search{position:absolute;right:100px;top:4px;width:40px;height:40px;background:var(--tan)}

/* hero */
.hero{top:174px;height:516px}
.hero .photo{position:absolute;inset:0;background:linear-gradient(120deg,#dfe4ea 0%,#b7c2cf 35%,#8d9cb0 65%,#5f7089 100%)}
.hero .caption{position:absolute;left:0;bottom:0;width:600px;height:122px;background:rgba(38,52,79,.85);clip-path:polygon(0 0,96% 0,100% 100%,0 100%);padding:24px 0 0 100px;color:var(--white)}
.hero .caption h2{font-family:'Cinzel',serif;font-weight:400;font-size:26px;letter-spacing:1px}
.hero .caption p{font-size:12px;line-height:17px;margin-top:6px;width:460px}
.hero .arrows{position:absolute;right:100px;bottom:22px;display:flex;gap:12px}

/* courses */
.courses{top:690px;height:534px;background:var(--grey)}
.courses .heading{margin-top:50px}
.course{position:absolute;top:107px;width:316px;text-align:center}
.course .photo{height:243px;border:5px solid var(--navy);background:linear-gradient(135deg,#cfd8e2,#8ea2b9)}
.course h3{font-family:'Cinzel',serif;font-weight:400;font-size:20px;color:var(--navy);margin-top:20px;line-height:26px;letter-spacing:1px;height:54px}
.course .btn{margin-top:12px}
.side-arrow{position:absolute;top:320px}

/* about */
.about{top:1224px;height:329px;background:var(--white)}
.about .heading{margin-top:36px}
.about .lead{width:1000px;margin:22px auto 0;text-align:center;font-size:13px;line-height:20px}
.pillars{position:absolute;top:170px;left:100px;width:1000px;display:flex;justify-content:space-between}
.pillar{display:flex;gap:16px;width:300px}
.pillar .icon{width:95px;height:95px;border-radius:50%;background:var(--navy);border:6px solid #dfe3ea;flex:none}
.pillar h4{font-family:'Cinzel',serif;font-size:20px;color:#222;margin-top:8px}
.pillar p{font-size:13px;line-height:18px;margin-top:4px}

/* why */
.why{top:1553px;height:742px;background:var(--grey)}
.why .heading{margin-top:34px}
.why-brand{position:absolute;left:120px;top:370px;width:280px;display:flex;align-items:center;gap:12px}
.why-brand .mark{width:44px;height:44px;background:var(--navy);flex:none}
.why-brand .brand-name{font-size:19px;line-height:23px}
.why-item{position:absolute;width:520px}
.why-item h4{font-size:17px;color:var(--navy);font-weight:700}
.why-item p{font-size:14px;line-height:19px;color:#444;margin-top:3px}

/* testimonials */
.testimonials{top:2295px;height:345px;background:var(--white)}
.testimonials .heading{margin-top:40px}
.testimonials .quote{position:absolute;top:222px;left:100px;width:1000px;text-align:center;font-style:italic;font-size:13px;line-height:25px;color:#555}

/* split */
.split{top:2640px;height:339px}
.split .half{position:absolute;top:0;width:600px;height:339px;padding:58px 0 0 100px;color:var(--white)}
.split .candidate{left:0;background:linear-gradient(90deg,#2d3d5e,#4a5c80)}
.split .employer{left:600px;background:linear-gradient(90deg,#c8a577,#dcc4a2);padding-left:150px}
.split h3{font-family:'Cinzel',serif;font-weight:400;font-size:30px;display:flex;align-items:center;gap:10px}
.split h3 .ic{width:24px;height:24px;border-radius:50%;background:var(--white)}
.split p{font-size:13px;line-height:19px;width:330px;margin-top:16px}
.split .btn{background:transparent;border:1px solid var(--white);margin-top:22px}
.seal{position:absolute;left:520px;top:90px;width:160px;height:160px;border-radius:50%;background:var(--white);border:5px solid #ccd3de;display:flex;align-items:center;justify-content:center;text-align:center;padding:20px}
.seal .brand-name{font-size:15px;line-height:19px}

/* blog */
.news{top:2979px;height:411px;background:var(--white)}
.news h3{position:absolute;top:58px;font-family:'Cinzel',serif;font-weight:400;font-size:25px;color:var(--navy);letter-spacing:1px}
.news h3 .accent{color:var(--tan)}
.news .rule{position:absolute;top:94px;height:2px;background:var(--navy)}
.blog-card{position:absolute;left:100px;top:139px;width:475px;height:212px;border:1px solid #ddd;box-shadow:0 2px 5px rgba(0,0,0,.12)}
.blog-card .photo{position:absolute;left:0;top:0;width:170px;height:210px;background:linear-gradient(135deg,#e4e9ef,#8ea0b7)}
.blog-card .body{position:absolute;left:190px;top:26px;width:265px}
.blog-card h4{font-size:15px;color:#222}
.blog-card p{font-size:13px;line-height:18px;margin-top:8px}
.blog-card .btn{background:var(--tan);padding:8px 16px;margin-top:12px;font-size:12px}
.date{position:absolute;left:492px;top:113px;width:66px;height:56px;background:var(--tan);color:var(--white);text-align:center;padding-top:4px}
.date b{font-size:24px;display:block;line-height:28px}
.date span{font-size:12px}
.tweet{position:absolute;left:634px;width:466px;height:58px;border-bottom:1px solid #e2e2e2}
.tweet .av{position:absolute;left:0;top:4px;width:44px;height:40px;border:1px solid #ccc;background:#eef1f5}
.tweet .t{position:absolute;left:60px;top:0;width:330px;font-size:11px;line-height:14px}
.tweet .t b{color:#222}
.tweet .t em{color:#1da0e0;font-style:normal}
.tweet .d{position:absolute;right:36px;top:0;font-size:11px;color:#666}
.follow{position:absolute;left:1030px;top:68px;width:70px;height:22px;border:1px solid #ccc;border-radius:3px;font-size:11px;text-align:center;line-height:20px;color:#333}

/* enrol */
.enrol{top:3390px;height:176px}
.enrol .photo{position:absolute;inset:0;background:linear-gradient(90deg,#e9e9e9 0%,#d3d6da 60%,#b9bec6 100%)}
.enrol h3{position:absolute;left:100px;top:50px;width:740px;font-family:'Lato',sans-serif;font-weight:700;font-size:22px;line-height:36px;color:var(--navy)}
.enrol .book{position:absolute;left:893px;top:58px;width:207px;height:60px;background:var(--tan);color:var(--white);font-size:18px;font-weight:700;text-align:center;line-height:60px}

/* footer */
.footer{top:3566px;height:356px;background:#ececec}
.footer .panel{position:absolute;left:470px;top:0;width:730px;height:356px;background:var(--navy);clip-path:polygon(22px 0,100% 0,100% 100%,0 100%)}
.footer h3{position:absolute;top:30px;font-family:'Cinzel',serif;font-weight:400;font-size:24px;letter-spacing:1px}
.footer .rule{position:absolute;top:66px;height:1px}
.field{position:absolute;left:100px;width:315px;height:36px;background:var(--white);border:1px solid #d4d4d4;font-size:12px;color:#555;padding:10px 12px}
.submit{position:absolute;left:100px;top:308px;width:110px;height:38px;background:var(--navy);color:var(--white);font-size:13px;text-align:center;line-height:38px}
.links{position:absolute;top:96px;list-style:none;color:var(--white);font-size:13px}
.links li{margin-bottom:17px;padding-left:14px;position:relative;white-space:nowrap}
.links li::before{content:"";position:absolute;left:0;top:6px;width:5px;height:5px;border-radius:50%;background:var(--white)}
.contact{position:absolute;left:858px;color:var(--white);font-size:13px;line-height:18px;display:flex;gap:14px}
.contact .ic{width:26px;height:26px;background:var(--white);border-radius:50%;flex:none}
.foot-social{position:absolute;left:886px;top:300px;display:flex;gap:8px}
.foot-social span{width:32px;height:32px;border-radius:50%;background:var(--white);display:block}
.copyright{top:3922px;height:25px;background:var(--navy-dark);color:#dfe3ea;font-size:11px;text-align:right;padding:6px 230px 0 0}
</style>
</head>
<body>

<section class="section topbar">
  <div class="social" style="left:100px"><span></span><span></span><span></span><span></span></div>
  <div class="info" style="left:380px"><span class="dot-icon"></span>+61 (07) 5550 1234</div>
  <div class="info" style="left:555px"><span class="dot-icon"></span>INFO@KESTRELHEALTH.EXAMPLE</div>
  <div class="account"><span><span class="flag"></span>ENGLISH ▾</span><span>LOG IN / REGISTER</span></div>
</section>

<header class="section header">
  <div class="brand"><span class="mark"></span><span class="brand-name">Kestrel Institute of Training</span></div>
  <nav class="mainnav"><span>HOME</span><span>ABOUT US</span><span>COURSES</span><span>RECRUITMENT</span><span>CLASS SCHEDULE</span></nav>
</header>

<nav class="section subnav">
  <ul><li>TRAINEESHIPS QUEENSLAND FUNDING</li><li>LATEST NEWS BLOG</li><li>CORPORATE TRAINING</li><li>CONTACT US</li></ul>
  <div class="search"><svg width="40" height="40"><circle cx="18" cy="18" r="7" fill="none" stroke="#fff" stroke-width="2"/><line x1="23" y1="23" x2="29" y2="29" stroke="#fff" stroke-width="2"/></svg></div>
</nav>

<section class="section hero">
  <div class="photo" role="img" aria-label="Trainer presenting to a group of adult students in a bright classroom"></div>
  <div class="caption">
    <h2>Courses for Busy People</h2>
    <p>Our unique FastTrack CAT (Combined Assessment &amp; Training) class format delivers accelerated training that's specifically targeted at busy professionals...</p>
  </div>
  <div class="arrows">
    <svg width="14" height="20"><polyline points="11,3 4,10 11,17" fill="none" stroke="#fff" stroke-width="2"/></svg>
    <svg width="14" height="20"><polyline points="3,3 10,10 3,17" fill="none" stroke="#fff" stroke-width="2"/></svg>
  </div>
</section>

<section class="section courses">
  <h2 class="heading"><span class="accent">Our</span> Courses</h2>
  <div class="heading-rule"></div>
  <svg class="side-arrow" style="left:30px" width="30" height="60"><polyline points="26,4 6,30 26,56" fill="none" stroke="#999" stroke-width="2"/></svg>
  <svg class="side-arrow" style="left:1140px" width="30" height="60"><polyline points="4,4 24,30 4,56" fill="none" stroke="#999" stroke-width="2"/></svg>
  <div class="course" style="left:100px">
    <div class="photo" role="img" aria-label="Reception staff team smiling in an office"></div>
    <h3>Medical Reception<br>&amp; Terminology</h3><span class="btn">Read More</span>
  </div>
  <div class="course" style="left:442px">
    <div class="photo" role="img" aria-label="Group of young business administration students"></div>
    <h3>Cert III Business<br>Administration</h3><span class="btn">Read More</span>
  </div>
  <div class="course" style="left:785px">
    <div class="photo" role="img" aria-label="Medical terminology textbook with stethoscope" style="background:linear-gradient(135deg,#e8dccb,#b98c6e)"></div>
    <h3>Medical<br>Terminology</h3><span class="btn">Read More</span>
  </div>
</section>

<section class="section about">
  <h2 class="heading"><span class="accent">About</span> Us</h2>
  <div class="heading-rule"></div>
  <p class="lead">Kestrel is Australia's Leading Provider of Educational, Training and Support Services for the Medical and Dental industry – enabling students to be immediately skilled and 'Job Ready' for a career in Health. Kestrel is a Registered Training Organisation offering specialised Medical Administration Training in over 15 locations Australia wide... [ + ]</p>
  <div class="pillars">
    <div class="pillar"><span class="icon"></span><div><h4>Story</h4><p>Kestrel Health Management started business in February 1999 primarily.... [ + ]</p></div></div>
    <div class="pillar"><span class="icon"></span><div><h4>Vision</h4><p>To be Australia's Leading Educational supplier in our Core Units.... [ + ]</p></div></div>
    <div class="pillar"><span class="icon"></span><div><h4>Core Values</h4><p>The Kestrel business is always evolving and as we do, we aim to be true ... [ + ]</p></div></div>
  </div>
</section>

<section class="section why">
  <h2 class="heading"><span class="accent">Why Choose</span> Us</h2>
  <div class="heading-rule"></div>
  <svg width="1200" height="742" style="position:absolute;left:0;top:0">
    <path d="M300 167 Q560 407 300 687" fill="none" stroke="#c9c9c9" stroke-width="8"/>
    <g stroke="#b5b5b5" stroke-width="2" fill="none">
      <polyline points="347,216 420,160 460,140"/>
      <polyline points="409,315 500,315 545,263"/>
      <line x1="430" y1="417" x2="605" y2="368"/>
      <polyline points="409,523 500,523 539,494"/>
      <polyline points="347,632 430,632 486,618"/>
    </g>
    <g fill="#fff" stroke="#b5b5b5" stroke-width="2">
      <circle cx="347" cy="216" r="6"/><circle cx="409" cy="315" r="6"/><circle cx="430" cy="417" r="6"/><circle cx="409" cy="523" r="6"/><circle cx="347" cy="632" r="6"/>
      <circle cx="307" cy="180" r="5"/><circle cx="378" cy="262" r="5"/><circle cx="425" cy="366" r="5"/><circle cx="425" cy="470" r="5"/><circle cx="380" cy="578" r="5"/><circle cx="310" cy="675" r="5"/>
    </g>
    <g fill="#34466b" stroke="#fff" stroke-width="4">
      <circle cx="500" cy="140" r="40"/><circle cx="584" cy="263" r="40"/><circle cx="645" cy="368" r="40"/><circle cx="579" cy="494" r="40"/><circle cx="526" cy="618" r="40"/>
    </g>
  </svg>
  <div class="why-brand"><span class="mark"></span><span class="brand-name">Kestrel Institute of Training</span></div>
  <div class="why-item" style="left:553px;top:104px"><h4>Quality</h4><p>Kestrel delivery quality, effective training facilitated by industry leaders. Just ask our students who rate us on average of 4.7 out of 5.</p></div>
  <div class="why-item" style="left:652px;top:222px;width:470px"><h4>Experience</h4><p>Kestrel is Australia's largest and leading providers of nationally recognised training in health administration – training from over 17 locations Australia wide.</p></div>
  <div class="why-item" style="left:710px;top:336px;width:420px"><h4>Value</h4><p>Our innovative teaching approach allows us to deliver exceptional training at affordable prices with no hidden extras.</p></div>
  <div class="why-item" style="left:650px;top:460px;width:470px"><h4>Industry Recognised</h4><p>Kestrel work hand in hand with industry to develop our core programme and consolidate the programme annually to keep the programme fresh and relevant.</p></div>
  <div class="why-item" style="left:595px;top:580px"><h4>Great Job Results</h4><p>Kestrel students get jobs! Our focus is to create job-ready students who are mentored to achieve their goals. Kestrel also provide a recruitment service for industry and graduates.</p></div>
</section>

<section class="section testimonials">
  <h2 class="heading"><span class="accent">Clients</span> Testimonials</h2>
  <div class="heading-rule"></div>
  <svg style="position:absolute;left:305px;top:132px" width="20" height="34"><polyline points="16,3 4,17 16,31" fill="none" stroke="#aaa" stroke-width="2"/></svg>
  <svg style="position:absolute;left:872px;top:132px" width="20" height="34"><polyline points="4,3 16,17 4,31" fill="none" stroke="#aaa" stroke-width="2"/></svg>
  <svg width="1200" height="200" style="position:absolute;left:0;top:100px">
    <circle cx="416" cy="47" r="44" fill="#9aa8bb" stroke="#34466b" stroke-width="5" role="img" aria-label="Portrait of a student"/>
    <circle cx="540" cy="47" r="42" fill="#c9a88a" stroke="#ddd" stroke-width="3" role="img" aria-label="Portrait of a student"/>
    <circle cx="663" cy="47" r="42" fill="#b7bcc4" stroke="#ddd" stroke-width="3" role="img" aria-label="Portrait of a student"/>
    <circle cx="784" cy="47" r="42" fill="#a9957f" stroke="#ddd" stroke-width="3" role="img" aria-label="Portrait of a student"/>
  </svg>
  <p class="quote">&ldquo; I completed the course on Feb 13th. Loved it. The trainers, Maree and Jo were excellent in their delivery and knowledge. I want to say a huge thank you for the course and knowledge I came away with. I have secured a fantastic job after my first application! Such good value for money too! I would highly recommend it. I'm a mature age person so it's never too late to up-skill yourself to get what you deserve! &rdquo;</p>
</section>

<section class="section split">
  <div class="half candidate" role="img" aria-label="Candidate in an office, navy toned">
    <h3><span class="ic"></span>For the Candidate</h3>
    <p><b>Looking for a Career in Medical Administration?</b><br>Our partner company, Kestrel Institute of Training has been the market leader in Medical Reception Training in Australia for over 17 years. In fact, we pioneered.</p>
    <span class="btn">Read More</span>
  </div>
  <div class="half employer" role="img" aria-label="Employer at work, warm toned">
    <h3><span class="ic"></span>For the Employer</h3>
    <p>Kestrel Recruitment is a Leading National Health Specialist Recruitment Agency with expertise in Medical and Dental administration recruitment for both permanent and temporary staff.</p>
    <span class="btn">Read More</span>
  </div>
  <div class="seal"><span class="brand-name">Kestrel Institute of Training</span></div>
</section>

<section class="section news">
  <h3 style="left:100px"><span class="accent">Latest</span> Blog</h3>
  <div class="rule" style="left:100px;width:170px"></div>
  <span style="position:absolute;left:540px;top:66px;font-size:16px;color:#333;font-weight:700">&lt; &gt;</span>
  <div class="date"><b>26</b><span>June</span></div>
  <div class="blog-card">
    <div class="photo" role="img" aria-label="Smiling businessman in a suit"></div>
    <div class="body">
      <h4>Lorem ipsum do sit amet,</h4>
      <p>Lorem ipsum dolor sit amet, consectetur adipiscing elit, sed do eiusmod tempor incididunt ut labore et dolore magna aliqua. Ut enim ad minim veniam.</p>
      <span class="btn">Read More</span>
    </div>
  </div>
  <h3 style="left:634px"><span class="accent">Latest</span> Tweets</h3>
  <div class="rule" style="left:634px;width:200px"></div>
  <div class="follow">Follow</div>
  <div class="tweet" style="top:152px"><span class="av"></span><div class="t"><b>Kestrel</b> <em>@KestrelTraining</em><br>Lorem ipsum dolor sit amet, consectetur adipiscing elit, sed di nonummy nibh euismod tincidunt ut laoreet dolore ma</div><span class="d">20 June</span></div>
  <div class="tweet" style="top:222px"><span class="av"></span><div class="t"><b>Kestrel</b> <em>@KestrelTraining</em><br>Lorem ipsum dolor sit amet, consectetur adipiscing elit, sed di nonummy nibh euismod tincidunt ut laoreet dolore ma</div><span class="d">20 June</span></div>
  <div class="tweet" style="top:290px;border:0"><span class="av"></span><div class="t"><b>Kestrel</b> <em>@KestrelTraining</em><br>Lorem ipsum dolor sit amet, consectetur adipiscing elit, sed di nonummy nibh euismod tincidunt ut laoreet dolore ma</div><span class="d">20 June</span></div>
</section>

<section class="section enrol">
  <div class="photo" role="img" aria-label="Faded office team meeting background"></div>
  <h3>Enrol In Our BSB51915 Diploma Of Leadership And Managemenr And Gain Vaaluable Skills To Launch Your Management Career.</h3>
  <div class="book">Booking Now</div>
</section>

<footer class="section footer">
  <h3 style="left:100px;color:#222">EMAIL me an Info Pack</h3>
  <div class="rule" style="left:100px;width:315px;background:#999"></div>
  <div class="field" style="top:86px">Name</div>
  <div class="field" style="top:130px">Email</div>
  <div class="field" style="top:174px">Course</div>
  <div class="field" style="top:218px;height:72px">State</div>
  <div class="submit">Submit</div>
  <div class="panel"></div>
  <h3 style="left:490px;color:#fff">Quick Links</h3>
  <div class="rule" style="left:490px;width:310px;background:#8a97b0"></div>
  <ul class="links" style="left:490px"><li>Home</li><li>About Us</li><li>Courses</li><li>Recruitment</li><li>Class Schedule</li><li>Traineeships Queensland Funding</li></ul>
  <ul class="links" style="left:640px"><li>Latest News Blog</li><li>Corporate Training</li><li>Contact Us</li></ul>
  <h3 style="left:858px;color:#fff">Contact Us</h3>
  <div class="rule" style="left:858px;width:242px;background:#8a97b0"></div>
  <div class="contact" style="top:96px"><span class="ic"></span><div><b>Kestrel Health Trainings</b><br>123, Ut wisi enim ad minim ve,<br>Mor nostrui tation - 123 456</div></div>
  <div class="contact" style="top:172px"><span class="ic"></span><div style="padding-top:4px">+61 (07) 5550 1234</div></div>
  <div class="contact" style="top:226px"><span class="ic"></span><div style="padding-top:4px">info@kestrelhealth.example</div></div>
  <div class="foot-social"><span></span><span></span><span></span><span></span></div>
</footer>

<div class="section copyright">Copyright © 2016 Kestrel Health Trainings. All Right Reserved</div>

</body>
</html>
```